VORLAND COMPOSITES INC website in USA

VORLAND COMPOSITES INC incorporated and operated in USA needs a completely new design of website. This Wyoming based company is a importer and distributor of composites material to supply mainly to American and Canadian/Mexican customers. Our main products includes Carbon Fiber, Aramid Fiber, Glass Fiber, Basalt Fiber, High Silica Glass, Quartz Fiber, S-Glass, Alumina Fiber, Vacuum Auxiliary.

We are one stop composites solution provider for Automotive, Aerospace, Construction, Electrical and Machinery industries.

We are exclusive sales company in North America for BLORAN composites produced from China and their other Asia facilities.

Target Market(s)

USA and Canada

Industry/Entity Type

Composites materials

Coding

Coded - Design and coding required

Number of Pages Required

5+ page

Requirements
Nice to have
• Color theme to match our corporate logo VORLAND. VORLAND stands for Northgate Provisioning Trade Holdings

```html
<!DOCTYPE html>
<html lang="en">
<head>
<meta charset="utf-8">
<title>Vorland Composites Inc</title>
<link rel="stylesheet" href="https://fonts.googleapis.com/css2?family=Montserrat:wght@600;700;800&family=Lato:wght@400;700&display=swap">
<style>
:root{
  --orange:#e8822a;
  --orange-dark:#d9701b;
  --ink:#2b2624;
  --text:#3a3a3a;
  --muted:#555;
  --light:#e4e4e4;
  --card:#ffffff;
  --line:#d8d8d8;
}
*{box-sizing:border-box;margin:0;padding:0}
html,body{width:1200px;height:4605px;overflow:hidden}
body{font-family:"Lato",sans-serif;color:var(--text);background:#fff;position:relative}
.abs{position:absolute}
h1,h2,h3,h4{font-family:"Montserrat",sans-serif}
.btn{position:absolute;display:flex;align-items:center;justify-content:center;background:var(--orange);color:#fff;font-family:"Lato",sans-serif;font-weight:700;font-size:15px;border-radius:3px;text-decoration:none;white-space:nowrap}

/* top bar */
.topbar{position:absolute;left:0;top:0;width:1200px;height:43px;background:var(--ink);color:#fff;font-size:14px}
.topbar .item{position:absolute;top:12px;display:flex;align-items:center;gap:14px;white-space:nowrap}
.topbar svg{width:22px;height:18px}

/* nav */
.nav{position:absolute;top:43px;left:0;width:1200px;height:86px;background:#fff}
.logo{position:absolute;left:111px;top:11px;height:64px;display:flex;align-items:center;gap:14px}
.logo .mark{width:18px;height:18px;background:var(--orange);border-radius:50%}
.logo .name{font-family:"Montserrat",sans-serif;font-weight:800;font-size:30px;color:var(--orange);letter-spacing:-1px}
.logo .rule{width:1px;height:46px;background:#999}
.logo .sub{font-size:9px;line-height:11px;color:#444;width:80px}
.menu a{position:absolute;top:33px;font-size:14px;color:#333;text-decoration:none;white-space:nowrap}
.menu a.active{color:var(--orange)}

/* hero */
.hero{position:absolute;top:129px;left:0;width:1200px;height:690px;overflow:hidden}
.hero .photo{position:absolute;inset:0;background:linear-gradient(120deg,#0c0c0c 0%,#1e1e1e 40%,#2e2c2a 60%,#141414 100%)}
.hero h1{position:absolute;left:111px;top:120px;color:#fff;font-size:41px;line-height:56px;font-weight:700}
.hero h1 span{color:var(--orange)}
.hero p{position:absolute;left:111px;top:308px;width:480px;color:#fff;font-size:19px;line-height:30px}
.dots{position:absolute;display:flex;gap:6px}
.dots i{display:block;width:19px;height:5px;background:#fff;border-radius:1px}
.dots i.on{background:var(--orange)}
.dots.grey i{background:#ddd}
.dots.grey i.on{background:var(--orange)}

/* section headings */
.sec-title{position:absolute;left:0;width:1200px;text-align:center;font-size:37px;font-weight:700;color:var(--ink)}
.underline{position:absolute;width:64px;height:3px;background:var(--orange);left:568px}
.sec-sub{position:absolute;left:0;width:1200px;text-align:center;font-size:16px;line-height:26px;color:#333}

/* product cards */
.arrow{position:absolute;width:36px;height:36px;border-radius:50%;background:var(--ink)}
.arrow svg{width:36px;height:36px}
.pcard{position:absolute;top:1064px;width:310px;height:402px;background:var(--card);border:2px solid var(--line);border-radius:6px;overflow:hidden;text-align:center}
.pcard .img{position:absolute;left:0;top:0;width:100%;height:200px}
.pcard .curve{position:absolute;left:0;top:176px;width:100%;height:40px}
.pcard .icon{position:absolute;left:115px;top:174px;width:76px;height:76px;border-radius:50%;background:var(--ink);border:4px solid #fff;display:flex;align-items:center;justify-content:center}
.pcard .icon svg{width:36px;height:36px}
.pcard h3{position:absolute;top:271px;width:100%;font-family:"Lato",sans-serif;font-weight:700;font-size:23px;color:var(--ink)}
.pcard p{position:absolute;top:318px;left:25px;right:25px;font-size:14.5px;line-height:24px;color:#444}
.pcard.featured{background:var(--orange);border-color:var(--orange)}
.pcard.featured h3,.pcard.featured p{color:#fff}
.pcard.featured .icon{background:#fff;border-color:var(--orange)}

/* about */
.about{position:absolute;top:1584px;left:0;width:1200px;height:580px;background:#e2e2e2}
.about .band{position:absolute;left:0;top:0;width:334px;height:580px;background:var(--orange)}
.about .circle{position:absolute;left:111px;top:74px;width:432px;height:432px;border-radius:50%;border:5px solid #fff;background:radial-gradient(circle at 40% 40%,#6a6a6e 0%,#3a3a3e 45%,#1a1a1c 100%)}
.about h2{position:absolute;left:610px;top:85px;font-size:37px;font-weight:700;color:var(--ink)}
.about .underline{left:610px;top:137px}
.about p{position:absolute;left:610px;width:478px;font-size:15.5px;line-height:26px;color:#333;text-align:justify}

/* industries */
.icard{position:absolute;top:2425px;width:231px;height:227px;background:#e4e4e4;border-radius:4px;text-align:center}
.icard .ic{position:absolute;left:87px;top:36px;width:57px;height:57px;border-radius:50%;background:#fff;border:4px solid #f3c49a;display:flex;align-items:center;justify-content:center}
.icard .ic span{width:38px;height:38px;border-radius:50%;background:var(--orange);display:flex;align-items:center;justify-content:center}
.icard .ic svg{width:22px;height:22px}
.icard h4{position:absolute;top:108px;width:100%;font-family:"Lato",sans-serif;font-weight:700;font-size:17px;color:#222}
.icard p{position:absolute;top:143px;left:16px;right:16px;font-size:12.5px;line-height:17px;color:#555}
.icard.featured{background:var(--orange)}
.icard.featured h4,.icard.featured p{color:#fff}
.icard.featured .ic span{background:#fff}

/* client */
.client{position:absolute;top:2821px;left:0;width:1200px;height:496px;background:linear-gradient(120deg,#e98a35 0%,#e07c26 45%,#d46f1c 70%,#e48230 100%)}
.client h2{position:absolute;top:90px;width:100%;text-align:center;color:#fff;font-size:37px;font-weight:700}
.client p{position:absolute;top:187px;left:220px;width:760px;text-align:center;color:#fff;font-size:15.5px;line-height:26px}
.client .brand{position:absolute;top:282px;left:0;width:100%;display:flex;justify-content:center;align-items:center;gap:12px}
.client .brand i{width:26px;height:26px;background:#fff}
.client .brand b{font-family:"Lato",sans-serif;font-weight:700;font-size:26px;color:#fff;letter-spacing:1px}
.client .btn{left:494px;top:358px;width:214px;height:40px;background:var(--ink);font-size:14.5px}

/* blog */
.bcard{position:absolute;top:3578px;width:310px;height:404px;background:#fff;border:2px solid var(--line);border-radius:6px;text-align:center}
.bcard .media{position:absolute;left:0;top:0;width:100%;height:226px;overflow:hidden;border-radius:4px 4px 0 0}
.bcard .img{position:absolute;left:0;top:0;width:100%;height:208px}
.bcard .curve{position:absolute;left:0;top:186px;width:100%;height:40px}
.bcard h3{position:absolute;top:247px;width:100%;font-family:"Lato",sans-serif;font-weight:700;font-size:23px;color:var(--ink)}
.bcard p{position:absolute;top:294px;left:25px;right:25px;font-size:14.5px;line-height:24px;color:#444}
.bcard .btn{left:89px;top:379px;width:128px;height:40px}

/* footer */
.footer{position:absolute;left:0;top:4110px;width:1200px;height:495px}
.footer .bg{position:absolute;inset:0;width:1200px;height:495px}
.footer h4{position:absolute;top:157px;color:#fff;font-size:20px;font-weight:700}
.footer a,.footer .t{position:absolute;color:#fff;font-size:14.5px;text-decoration:none;line-height:25px;white-space:nowrap}
.footer .t.wrap{white-space:normal}
.footer svg.ico{position:absolute;width:20px;height:20px}
.footer .rule{position:absolute;left:111px;top:453px;width:976px;height:1px;background:#555}
.footer .copy{position:absolute;top:468px;width:100%;text-align:center;color:#fff;font-size:13px}
</style>
</head>
<body>

<header class="topbar">
  <div class="item" style="left:229px">
    <svg viewBox="0 0 22 16"><rect x="0" y="0" width="22" height="16" rx="1" fill="#e8822a"/><path d="M0 0 L11 9 L22 0" fill="none" stroke="#2b2624" stroke-width="2"/></svg>
    SALES@VORLAND.EXAMPLE
  </div>
  <div class="item" style="left:531px">
    <svg viewBox="0 0 24 24"><path d="M6 2 L10 6 L8 9 C9 12 12 15 15 16 L18 14 L22 18 L19 22 C10 21 3 14 2 5 Z" fill="#e8822a"/></svg>
    CANADA : 416-555-0142
  </div>
  <div class="item" style="left:797px">
    <svg viewBox="0 0 24 24"><path d="M6 2 L10 6 L8 9 C9 12 12 15 15 16 L18 14 L22 18 L19 22 C10 21 3 14 2 5 Z" fill="#e8822a"/></svg>
    USA : 307-555-0186
  </div>
</header>

<nav class="nav">
  <div class="logo">
    <span class="mark"></span>
    <span class="name">VORLAND</span>
    <span class="rule"></span>
    <span class="sub">Northgate Provisioning Trade Holdings</span>
  </div>
  <div class="menu">
    <a class="active" href="#" style="left:533px">Home</a>
    <a href="#" style="left:615px">About Us</a>
    <a href="#" style="left:721px">Products</a>
    <a href="#" style="left:822px">Industries</a>
    <a href="#" style="left:933px">News</a>
    <a href="#" style="left:1012px">Contact Us</a>
  </div>
</nav>

<section class="hero">
  <div class="photo" role="img" aria-label="Rolls of woven black carbon fiber fabric on cardboard cores"></div>
  <h1>HIGH-PERFORMANCE<br><span>FIBER SOLUTIONS</span> FOR<br>EVERY INDUSTRY</h1>
  <p>From aerospace to construction, we supply engineered composites that deliver unmatched strength, heat resistance, and reliability.</p>
  <a class="btn" href="#" style="left:111px;top:436px;width:204px;height:41px">Explore Our Products</a>
  <div class="dots" style="left:565px;top:604px"><i class="on"></i><i></i><i></i></div>
  <svg class="abs" style="left:0;top:540px" width="1200" height="150" viewBox="0 0 1200 150" preserveAspectRatio="none">
    <path d="M0 150 L0 100 Q600 230 1200 60 L1200 150 Z" fill="#fff"/>
    <path d="M0 100 Q600 230 1200 60 L1200 72 Q600 244 0 114 Z" fill="#e8822a"/>
  </svg>
</section>

<h2 class="sec-title" style="top:910px">Our Products</h2>
<div class="underline" style="top:964px"></div>
<p class="sec-sub" style="top:988px">Delivering a complete range of advanced composite materials — engineered for strength,<br>durability, and performance in every application.</p>

<div class="arrow" style="left:54px;top:1227px"><svg viewBox="0 0 36 36"><path d="M21 11 L14 18 L21 25" fill="none" stroke="#fff" stroke-width="3"/></svg></div>
<div class="arrow" style="left:1110px;top:1227px"><svg viewBox="0 0 36 36"><path d="M15 11 L22 18 L15 25" fill="none" stroke="#fff" stroke-width="3"/></svg></div>

<article class="pcard" style="left:111px">
  <div class="img" role="img" aria-label="Close-up of black carbon fiber weave" style="background:linear-gradient(135deg,#2a2a2a,#6d6d6d 50%,#1c1c1c)"></div>
  <svg class="curve" viewBox="0 0 310 40" preserveAspectRatio="none"><path d="M0 0 Q155 50 310 0 L310 40 L0 40 Z" fill="#fff"/><path d="M0 0 Q155 50 310 0 L310 6 Q155 56 0 6 Z" fill="#e8822a"/></svg>
  <div class="icon"><svg viewBox="0 0 24 24" fill="none" stroke="#e8822a" stroke-width="1.5"><path d="M12 3 L19 7 L19 15 L12 19 L5 15 L5 7 Z M5 7 L12 11 L19 7 M12 11 L12 19"/></svg></div>
  <h3>Carbon Fiber</h3>
  <p>Excepteur sint occaecat cupidatat non proident, sunt in culpa qui officia deserunt mollit laborum.</p>
</article>

<article class="pcard featured" style="left:445px">
  <div class="img" role="img" aria-label="Gold aramid fiber fabric gathered in folds" style="background:linear-gradient(135deg,#a98a3c,#e0c985 50%,#8a6e2c)"></div>
  <svg class="curve" viewBox="0 0 310 40" preserveAspectRatio="none"><path d="M0 0 Q155 50 310 0 L310 40 L0 40 Z" fill="#e8822a"/><path d="M0 0 Q155 50 310 0 L310 6 Q155 56 0 6 Z" fill="#fff"/></svg>
  <div class="icon"><svg viewBox="0 0 24 24" fill="none" stroke="#2b2624" stroke-width="1.5"><path d="M12 3 L19 6 L19 12 C19 16 16 19 12 21 C8 19 5 16 5 12 L5 6 Z"/><path d="M9 12 L11 14 L15 10"/></svg></div>
  <h3>Aramid Fiber</h3>
  <p>Excepteur sint occaecat cupidatat non proident, sunt in culpa qui officia deserunt mollit laborum.</p>
</article>

<article class="pcard" style="left:778px">
  <div class="img" role="img" aria-label="White glass fiber cloth in soft folds" style="background:linear-gradient(135deg,#b9b9b9,#ececec 50%,#9f9f9f)"></div>
  <svg class="curve" viewBox="0 0 310 40" preserveAspectRatio="none"><path d="M0 0 Q155 50 310 0 L310 40 L0 40 Z" fill="#fff"/><path d="M0 0 Q155 50 310 0 L310 6 Q155 56 0 6 Z" fill="#e8822a"/></svg>
  <div class="icon"><svg viewBox="0 0 24 24" fill="none" stroke="#e8822a" stroke-width="1.5"><path d="M10 4 L11.5 9 L16 10.5 L11.5 12 L10 17 L8.5 12 L4 10.5 L8.5 9 Z"/><path d="M17 13 L17.8 15.2 L20 16 L17.8 16.8 L17 19 L16.2 16.8 L14 16 L16.2 15.2 Z"/></svg></div>
  <h3>Glass Fiber</h3>
  <p>Excepteur sint occaecat cupidatat non proident, sunt in culpa qui officia deserunt mollit laborum.</p>
</article>

<section class="about">
  <div class="band"></div>
  <div class="circle" role="img" aria-label="Close-up of a frayed fiber fabric edge"></div>
  <h2>About Us</h2>
  <div class="underline"></div>
  <p style="top:180px">Lorem ipsum dolor sit amet, consectetur adipiscing elit, sed do eiusmod tempor incididunt ut labore et dolore magna aliqua. Ut enim ad minim veniam, quis nostrud exercitation ullamco laboris nisi ut aliquip ex ea commodo consequat.</p>
  <p style="top:308px">Duis aute irure dolor in reprehenderit in voluptate velit esse cillum dolore eu fugiat nulla pariatur. Excepteur sint occaecat cupidatat non proident, sunt in culpa qui officia deserunt mollit anim id est laborum.</p>
  <a class="btn" href="#" style="left:610px;top:447px;width:125px;height:40px">Read More</a>
</section>

<h2 class="sec-title" style="top:2260px">Industries We Serve</h2>
<div class="underline" style="top:2313px"></div>
<p class="sec-sub" style="top:2337px">Vorland Composites provides high-performance fibers and composite materials<br>to a diverse range of industries.</p>

<div class="icard" style="left:111px">
  <div class="ic"><span><svg viewBox="0 0 24 24" fill="none" stroke="#fff" stroke-width="1.6"><circle cx="12" cy="12" r="7"/><circle cx="12" cy="12" r="2.5"/></svg></span></div>
  <h4>Automotive</h4>
  <p>Excepteur sint occaecat at non proident, sunt in culpa qui officia deserunt mollit laborum.</p>
</div>
<div class="icard featured" style="left:359px">
  <div class="ic"><span><svg viewBox="0 0 24 24" fill="none" stroke="#2b2624" stroke-width="1.6"><path d="M12 3 L14 10 L21 13 L14 14 L12 21 L10 14 L3 13 L10 10 Z"/></svg></span></div>
  <h4>Aerospace</h4>
  <p>Excepteur sint occaecat at non proident, sunt in culpa qui officia deserunt mollit laborum.</p>
</div>
<div class="icard" style="left:608px">
  <div class="ic"><span><svg viewBox="0 0 24 24" fill="none" stroke="#fff" stroke-width="1.6"><rect x="5" y="6" width="14" height="13"/><path d="M5 10 H19 M9 6 V19 M15 6 V19"/></svg></span></div>
  <h4>Construction</h4>
  <p>Excepteur sint occaecat at non proident, sunt in culpa qui officia deserunt mollit laborum.</p>
</div>
<div class="icard" style="left:856px">
  <div class="ic"><span><svg viewBox="0 0 24 24" fill="none" stroke="#fff" stroke-width="1.6"><path d="M13 3 L6 13 H11 L10 21 L18 10 H13 Z"/></svg></span></div>
  <h4>Electrical</h4>
  <p>Excepteur sint occaecat at non proident, sunt in culpa qui officia deserunt mollit laborum.</p>
</div>
<div class="dots grey" style="left:565px;top:2692px"><i class="on"></i><i></i><i></i></div>

<section class="client" role="img" aria-label="Orange-toned photo of a worker handling composite material">
  <h2>Our Client</h2>
  <p>Vorland Composites is proud to be the exclusive distributor of BLORAN Composites in North America. Through this partnership, we provide high-quality, reliable composite materials sourced from BLORAN facilities in Asia.</p>
  <div class="brand"><i></i><b>BLORAN</b></div>
  <a class="btn" href="#">Explore BLORAN Products</a>
</section>

<h2 class="sec-title" style="top:3417px">Our Blog</h2>
<div class="underline" style="top:3471px"></div>
<p class="sec-sub" style="top:3495px">Delivering a complete range of advanced composite materials — engineered for strength,<br>durability, and performance in every application.</p>

<div class="arrow" style="left:54px;top:3734px"><svg viewBox="0 0 36 36"><path d="M21 11 L14 18 L21 25" fill="none" stroke="#fff" stroke-width="3"/></svg></div>
<div class="arrow" style="left:1110px;top:3734px"><svg viewBox="0 0 36 36"><path d="M15 11 L22 18 L15 25" fill="none" stroke="#fff" stroke-width="3"/></svg></div>

<article class="bcard" style="left:111px">
  <div class="media">
    <div class="img" role="img" aria-label="Stacked carbon fiber sheets" style="background:linear-gradient(160deg,#8a949c,#3a3f44 55%,#1d2023)"></div>
    <svg class="curve" viewBox="0 0 310 40" preserveAspectRatio="none"><path d="M0 0 Q155 50 310 0 L310 40 L0 40 Z" fill="#fff"/><path d="M0 0 Q155 50 310 0 L310 6 Q155 56 0 6 Z" fill="#e8822a"/></svg>
  </div>
  <h3>Lorem ipsum dolor</h3>
  <p>Excepteur sint occaecat cupidatat non proident, sunt in culpa qui officia deserunt mollit laborum.</p>
  <a class="btn" href="#">Read More</a>
</article>
<article class="bcard" style="left:445px">
  <div class="media">
    <div class="img" role="img" aria-label="Car assembly line in a factory" style="background:linear-gradient(160deg,#6f8aa6,#a9b6c2 50%,#8a4a46)"></div>
    <svg class="curve" viewBox="0 0 310 40" preserveAspectRatio="none"><path d="M0 0 Q155 50 310 0 L310 40 L0 40 Z" fill="#fff"/><path d="M0 0 Q155 50 310 0 L310 6 Q155 56 0 6 Z" fill="#e8822a"/></svg>
  </div>
  <h3>Lorem ipsum dolor</h3>
  <p>Excepteur sint occaecat cupidatat non proident, sunt in culpa qui officia deserunt mollit laborum.</p>
  <a class="btn" href="#">Read More</a>
</article>
<article class="bcard" style="left:778px">
  <div class="media">
    <div class="img" role="img" aria-label="Industrial machinery in a production hall" style="background:linear-gradient(160deg,#5c6166,#b8bcbf 50%,#7a7f83)"></div>
    <svg class="curve" viewBox="0 0 310 40" preserveAspectRatio="none"><path d="M0 0 Q155 50 310 0 L310 40 L0 40 Z" fill="#fff"/><path d="M0 0 Q155 50 310 0 L310 6 Q155 56 0 6 Z" fill="#e8822a"/></svg>
  </div>
  <h3>Lorem ipsum dolor</h3>
  <p>Excepteur sint occaecat cupidatat non proident, sunt in culpa qui officia deserunt mollit laborum.</p>
  <a class="btn" href="#">Read More</a>
</article>

<footer class="footer">
  <svg class="bg" viewBox="0 0 1200 495" preserveAspectRatio="none">
    <path d="M0 120 Q600 -30 1200 110 L1200 495 L0 495 Z" fill="#e8822a"/>
    <path d="M0 142 Q600 -6 1200 128 L1200 495 L0 495 Z" fill="#2b2624"/>
  </svg>
  <h4 style="left:111px">MAIN LINKS</h4>
  <a href="#" style="left:111px;top:204px">Home</a>
  <a href="#" style="left:111px;top:243px">About Us</a>
  <a href="#" style="left:111px;top:281px">Products</a>
  <a href="#" style="left:111px;top:320px">Industries</a>
  <a href="#" style="left:111px;top:358px">Connect Us</a>

  <h4 style="left:325px">USA</h4>
  <svg class="ico" style="left:325px;top:208px" viewBox="0 0 24 24" fill="none" stroke="#fff" stroke-width="1.6"><path d="M12 21 C7 15 5 12 5 9 A7 7 0 0 1 19 9 C19 12 17 15 12 21 Z"/><circle cx="12" cy="9" r="2.5"/></svg>
  <span class="t" style="left:366px;top:204px">112 CEDAR HOLLOW ST,<br>SHERIDAN, WY, USA 82801</span>
  <svg class="ico" style="left:325px;top:298px" viewBox="0 0 24 24" fill="none" stroke="#fff" stroke-width="1.6"><path d="M6 3 L10 7 L8 9.5 C9 12.5 11.5 15 14.5 16 L17 14 L21 18 L18.5 21 C10 20 4 14 3 5.5 Z"/></svg>
  <span class="t" style="left:366px;top:295px">307-555-0186</span>
  <svg class="ico" style="left:325px;top:358px" viewBox="0 0 24 24" fill="none" stroke="#fff" stroke-width="1.6"><rect x="3" y="5" width="18" height="14" rx="1"/><path d="M3 6 L12 13 L21 6"/></svg>
  <span class="t" style="left:366px;top:355px">SALES@VORLAND.EXAMPLE</span>

  <h4 style="left:647px">CANADA</h4>
  <svg class="ico" style="left:647px;top:208px" viewBox="0 0 24 24" fill="none" stroke="#fff" stroke-width="1.6"><path d="M12 21 C7 15 5 12 5 9 A7 7 0 0 1 19 9 C19 12 17 15 12 21 Z"/><circle cx="12" cy="9" r="2.5"/></svg>
  <span class="t wrap" style="left:688px;top:204px;width:220px">2210 Maple Crest Ave, Suite 400, Markham, ON, L4B 2K9, Canada</span>
  <svg class="ico" style="left:647px;top:306px" viewBox="0 0 24 24" fill="none" stroke="#fff" stroke-width="1.6"><path d="M6 3 L10 7 L8 9.5 C9 12.5 11.5 15 14.5 16 L17 14 L21 18 L18.5 21 C10 20 4 14 3 5.5 Z"/></svg>
  <span class="t" style="left:688px;top:303px">416-555-0142</span>
  <svg class="ico" style="left:647px;top:358px" viewBox="0 0 24 24" fill="none" stroke="#fff" stroke-width="1.6"><rect x="3" y="5" width="18" height="14" rx="1"/><path d="M3 6 L12 13 L21 6"/></svg>
  <span class="t" style="left:688px;top:355px">SALES@VORLAND.EXAMPLE</span>

  <h4 style="left:958px">OTHER LINKS</h4>
  <a href="#" style="left:958px;top:199px">Support</a>
  <a href="#" style="left:958px;top:238px">News &amp; Insights</a>
  <a href="#" style="left:958px;top:276px">Partnership</a>
  <a href="#" style="left:958px;top:315px">Terms &amp; conditions</a>
  <a href="#" style="left:958px;top:353px">Privacy policy</a>

  <div class="rule"></div>
  <p class="copy">Copyright © 2025 Vorland. All rights reserved.</p>
</footer>

</body>
</html>
```